Small corporate website template design

I need a couple templates designed for a small corporate website. The corporate site reflects the existence of the parent company which will own various brands/services that have their own websites, so it will mainly be used to present who we are, what we do, what is happening (news/events), how to contact us, link off to our other brand/service sites, as well as post information for public relations, investors, and job opportunities.

The company name is Brelvanto LLC (www.brelvanto-example.com), and the name is representative of stratified layers of interconnected digital services. The corporate site is not expected to generate a bunch of fanfare - that honor will be reserved for the externally linked brand/service sites.

The provided logo may be manipulated in color, size, shape, positioning, etc. to get it to fit with the design, but should be integrated in some way.

What we are looking for is a home page layout as well as a template for an inner page whereby the navigation/logo, etc may be diminished to some extent for the inner pages. We are also interested in reusable elements such as dividers, content containers, etc. in order to represent the types of information described above that we would like to present as described above.

We are particularly interested in consistency of design elements, conservative use of color (including consideration of accessibility concerns), judicious use of whitespace in favor of simplified messaging, and something lending itself well to internationalization/translation.

Target Market(s)

Small business owners, entrepreneurs (B2B)

Number of Pages Required

2 page

Font styles to use
Sans Serif

Requirements
Must have
• See the attached PDF with the logo concept, color swatches, and comparative sites.

```html
<!DOCTYPE html>
<html lang="en">
<head>
<meta charset="utf-8">
<title>Brelvanto LLC</title>
<link rel="stylesheet" href="https://fonts.googleapis.com/css2?family=Lato:wght@400;700;900&display=swap">
<style>
:root{
  --navy:#0f2a57;
  --blue:#2c5a95;
  --blue-deep:#234b83;
  --orange:#f7931e;
  --orange-deep:#c25a1a;
  --card:#ebebeb;
  --text:#3a3a3a;
  --muted:#6b6b6b;
  --line:#dcdcdc;
  --footer:#262626;
  --white:#ffffff;
}
*{box-sizing:border-box;margin:0;padding:0}
html,body{width:1200px;height:2206px;overflow:hidden}
body{position:relative;font-family:'Lato',sans-serif;background:var(--white);color:var(--text)}
.abs{position:absolute}

/* hero */
.hero-bg{left:0;top:0;width:1200px;height:700px}
.brand-mark{left:75px;top:62px;display:flex;align-items:center;gap:12px;color:var(--white);font-weight:700;font-size:33px}
.brand-mark .dot{width:40px;height:40px;border-radius:50%;background:var(--white)}
.main-nav{left:428px;top:58px;display:flex;align-items:center;gap:0}
.main-nav a{color:var(--white);text-decoration:none;font-size:14px;font-weight:700;padding:10px 16px;border-radius:20px;margin-right:1px}
.main-nav a.active{background:var(--orange);padding:10px 22px;margin-right:4px}
.hero-illustration{left:505px;top:170px;width:695px;height:520px;border-radius:0 0 0 260px / 0 0 0 80px;
  background:radial-gradient(circle at 55% 45%,#4a86c8 0%,#3568a8 45%,#2c5a95 100%)}

.intro-card{left:75px;top:353px;width:421px;height:505px;background:var(--card);border-radius:24px;box-shadow:0 4px 12px rgba(0,0,0,.22);padding:30px 31px}
.section-title{font-weight:900;color:var(--navy);font-size:46px;line-height:1.1}
.rule{width:100px;height:3px;background:var(--orange-deep);margin:16px 0 22px}
.intro-card p{font-size:14px;line-height:25px;margin-bottom:6px}
.btn{display:inline-flex;align-items:center;justify-content:center;width:182px;height:54px;border-radius:27px;
  background:linear-gradient(90deg,var(--blue-deep) 0%,#4f5a7a 45%,var(--orange) 100%);color:var(--white);font-weight:700;font-size:18px;text-decoration:none}
.intro-card .btn{position:absolute;left:28px;top:413px}

.brands-label{left:524px;top:722px;font-size:22px;font-weight:700;color:#444}
.brands-arrows{left:1102px;top:724px}
.brand-tile{top:779px;width:190px;height:79px;border:1px solid var(--line);border-radius:10px;display:flex;align-items:center;justify-content:center;gap:8px;font-size:25px;font-weight:700;color:#333}
.brand-tile .sq{width:20px;height:20px;background:var(--orange);border-radius:50%}

/* services */
.services{left:0;top:931px;width:1200px;height:549px;overflow:hidden;
  background:linear-gradient(100deg,#c35f1c 0%,#8c5a3c 40%,#4d5870 70%,#2c5590 100%)}
.services .sweep{position:absolute;left:-200px;top:60px;width:1200px;height:900px;border-radius:50%;background:rgba(255,255,255,.05)}
.services-head{position:absolute;left:0;width:1200px;text-align:center;color:var(--white)}
.services-head h2{font-weight:900;font-size:44px;margin-top:60px}
.services-head .rule{margin:14px auto 24px;width:100px;background:var(--white)}
.services-head p{font-size:14px}
.service-card{top:231px;width:330px;height:246px;background:var(--white);border-radius:10px;text-align:center;padding-top:21px}
.service-card .icon{width:96px;height:96px;border-radius:50%;border:3px solid var(--orange);margin:0 auto 20px;display:flex;align-items:center;justify-content:center}
.service-card h3{font-size:19px;font-weight:700;color:var(--blue-deep);margin-bottom:6px}
.service-card p{font-size:14px;line-height:23px;color:var(--muted);padding:0 34px}

/* blog */
.blog{left:75px;top:1540px;width:510px}
.blog h3{font-size:19px;line-height:28px;color:var(--blue-deep);font-weight:700;margin-bottom:12px}
.blog p{font-size:14px;line-height:26px}
.blog .btn{position:absolute;left:1px;top:308px}
.blog-photo{left:613px;top:1551px;width:513px;height:349px;border-radius:12px;
  background:radial-gradient(circle at 45% 65%,#9fc2d9 0%,#4e7d9a 30%,#1f3f57 70%,#0f2236 100%)}

/* footer */
.site-footer{left:0;top:1987px;width:1200px;height:219px;background:var(--footer);text-align:center}
.footer-nav{display:flex;justify-content:center;gap:34px;margin-top:52px}
.footer-nav a{color:var(--white);font-size:14px;font-weight:700;text-decoration:none}
.copyright{color:#8a8a8a;font-size:12px;margin-top:18px}
.social{display:flex;justify-content:center;gap:18px;margin-top:10px}
.social span{color:#9a9a9a;font-size:13px;font-weight:700}
</style>
</head>
<body>

<svg class="abs hero-bg" viewBox="0 0 1200 700" aria-hidden="true">
  <defs>
    <linearGradient id="heroGrad" x1="0" y1="0" x2="1" y2="1">
      <stop offset="0" stop-color="#2d5d9a"/>
      <stop offset="1" stop-color="#234b83"/>
    </linearGradient>
  </defs>
  <path d="M0 0 H1200 V690 H880 C700 690 580 640 505 615 L243 353 L0 115 Z" fill="url(#heroGrad)"/>
</svg>

<div class="abs hero-illustration" role="img" aria-label="Illustration of digital service icons around a hand holding a smartphone"></div>

<div class="abs brand-mark"><span class="dot"></span>Brelvanto</div>

<nav class="abs main-nav">
  <a class="active" href="#">Home</a>
  <a href="#">Who We Are</a>
  <a href="#">What We Do</a>
  <a href="#">Clients</a>
  <a href="#">What is Happening</a>
  <a href="#">Blog</a>
  <a href="#">Contact Us</a>
</nav>

<section class="abs intro-card">
  <h1 class="section-title">Who We Are</h1>
  <div class="rule"></div>
  <p>Lorem ipsum dolor sit amet, consectetur adipisicing elit, sed do eiusmod tempor incididunt ut labore et doloreasdes magna aliqua. Ut enim ad minim veniam, quis nostrud exercitation ullamco laboris nisi ut aliquip ex ea commodalo consequat. Duis aute irure dolor in reprehenderit in voluptate velit esse cillum dolore eu fugiat nulla pariatur.</p>
  <p>Excepteur sint occaecat cupidatat non proident, sunt in culpa qui officia deserunt mollit anim id est laborum.</p>
  <a class="btn" href="#">Read More</a>
</section>

<div class="abs brands-label">Brands:</div>
<svg class="abs brands-arrows" width="24" height="20" viewBox="0 0 24 20" aria-hidden="true">
  <path d="M8 4 L3 10 L8 16 M16 4 L21 10 L16 16" fill="none" stroke="#333" stroke-width="2.4" stroke-linecap="round"/>
</svg>
<div class="abs brand-tile" style="left:524px"><span class="sq"></span>Norvique</div>
<div class="abs brand-tile" style="left:730px"><span class="sq"></span>Talberon</div>
<div class="abs brand-tile" style="left:936px"><span class="sq"></span>Quenlyx</div>

<section class="abs services">
  <div class="sweep"></div>
  <div class="services-head">
    <h2>What We DO</h2>
    <div class="rule"></div>
    <p>Excepteur sint occaecat cupidatat non proident, sunt in culpa qui officia deserunt mollit anim id est &nbsp;laborum.</p>
  </div>
  <div class="abs service-card" style="left:75px">
    <div class="icon">
      <svg width="40" height="36" viewBox="0 0 40 36" aria-hidden="true">
        <circle cx="14" cy="20" r="8" fill="none" stroke="#234b83" stroke-width="6" stroke-dasharray="4 2.3"/>
        <circle cx="14" cy="20" r="3" fill="#234b83"/>
        <circle cx="30" cy="10" r="5" fill="none" stroke="#234b83" stroke-width="4" stroke-dasharray="3 1.8"/>
        <circle cx="31" cy="28" r="5" fill="none" stroke="#234b83" stroke-width="4" stroke-dasharray="3 1.8"/>
      </svg>
    </div>
    <h3>EIUSMOD TEMPOR</h3>
    <p>Sed ut perspiciatis unde omnis iste natus error sit voluptatem accusantium..</p>
  </div>
  <div class="abs service-card" style="left:435px">
    <div class="icon">
      <svg width="26" height="38" viewBox="0 0 26 38" aria-hidden="true">
        <path d="M13 2 A10 10 0 0 1 19 20 V26 H7 V20 A10 10 0 0 1 13 2 Z" fill="none" stroke="#234b83" stroke-width="3"/>
        <rect x="8" y="29" width="10" height="3" fill="#234b83"/>
        <rect x="10" y="34" width="6" height="3" fill="#234b83"/>
      </svg>
    </div>
    <h3>EIUSMOD TEMPOR</h3>
    <p>Sed ut perspiciatis unde omnis iste natus error sit voluptatem accusantium..</p>
  </div>
  <div class="abs service-card" style="left:795px">
    <div class="icon">
      <svg width="42" height="34" viewBox="0 0 42 34" aria-hidden="true">
        <path d="M16 2 C25 2 31 7 31 13 C31 19 25 24 16 24 C14 24 12 24 10 23 L3 27 L5 21 C2 19 1 16 1 13 C1 7 7 2 16 2 Z" fill="#234b83"/>
        <path d="M34 12 C38 14 41 17 41 21 C41 24 39 26 37 27 L39 32 L33 29 C31 30 29 30 27 30 C22 30 18 28 16 26 C26 26 33 20 34 12 Z" fill="#234b83"/>
      </svg>
    </div>
    <h3>EIUSMOD TEMPOR</h3>
    <p>Sed ut perspiciatis unde omnis iste natus error sit voluptatem accusantium..</p>
  </div>
</section>

<section class="abs blog">
  <h2 class="section-title">Blog Posts</h2>
  <div class="rule" style="margin:14px 0 26px"></div>
  <h3>Lorem ipsum dolor sit amet, consectetur adipisicing elit, sed do eiusmod tempor incididunt...</h3>
  <p>Ut enim ad minim veniam, quis nostrud exercitation ullamco laboris nisi ut aliquip ex ea commodalo consequat. Duis aute irure dolor in reprehenderit in voluptate velit esse cillum dolore eu fugiat nulla pariatur occaecat cupidatat non proident sunt in culpa qui...</p>
  <a class="btn" href="#">Read More</a>
</section>
<div class="abs blog-photo" role="img" aria-label="Photo of a hand using a smartphone with glowing digital icons rising above it"></div>

<footer class="abs site-footer">
  <nav class="footer-nav">
    <a href="#">Home</a>
    <a href="#">Who We Are</a>
    <a href="#">What We Do</a>
    <a href="#">Clients</a>
    <a href="#">What is Happening</a>
    <a href="#">Blog</a>
    <a href="#">Contact Us</a>
  </nav>
  <p class="copyright">Copyright © 2018 Brelvanto LLC, All Rights Reserved</p>
  <div class="social">
    <span>Linkra</span><span>Chirpo</span><span>Pixgram</span><span>Workly</span><span>Vidora</span>
  </div>
</footer>

</body>
</html>
```